Custom Woodworking and Rock Design

We specialize in original, high quality, wood and rock art. It’s should be self explanatory ask questions if you need. Your team designing a logo. Furniture is custom made to order. Rocks are designed depending on consumer needs. Wood and rock can also be combined for custom work. Painted rocks on vintage wood. Custom chairs and cabinets. Artistic rocks for multiple uses:garden, magnets, custom. All ideas and requests are welcome.

Target Market(s)

All

Contact Information for Business Card

Mara Voss
Talbertstonecraft@mailbrook.net

Font styles to use
Sans Serif

Requirements
Must have
• Clear lettering
Nice to have
• Eye catching
Should not have
• Blurr

```html
<!DOCTYPE html>
<html lang="en">
<head>
<meta charset="utf-8">
<title>Talbert Stonecraft – Business Card</title>
<link rel="stylesheet" href="https://fonts.googleapis.com/css2?family=Lato:ital,wght@0,400;0,700;0,900;1,400;1,700&display=swap">
<style>
  :root {
    --page-bg: #e9e6e1;
    --card-tan: #c49a6c;
    --card-charcoal: #404042;
    --brand-red: #e8262b;
    --ink: #404042;
    --card-w: 668px;
    --card-h: 390px;
  }
  * { margin: 0; padding: 0; box-sizing: border-box; }
  html, body {
    width: 1200px; height: 1200px; overflow: hidden;
    background: var(--page-bg);
    font-family: "Lato", sans-serif;
  }
  .canvas { position: relative; width: 1200px; height: 1200px; }
  .card {
    position: absolute; left: 268px;
    width: var(--card-w); height: var(--card-h);
    border-radius: 20px; overflow: hidden;
    box-shadow: 0 3px 8px rgba(0,0,0,.25);
  }
  .card--front { top: 166px; background: var(--card-tan); }
  .card--back { top: 606px; background: var(--card-charcoal); }
  .front-disc {
    position: absolute; left: 333px; top: -36px;
    width: 462px; height: 462px; border-radius: 50%;
    background: var(--card-charcoal);
  }
  .company-line {
    position: absolute; left: 22px; top: 80px;
    font-style: italic; font-size: 24px; color: var(--ink);
  }
  .person-name {
    position: absolute; left: 22px; top: 142px;
    font-style: italic; font-size: 23px; letter-spacing: .5px; color: var(--ink);
  }
  .person-role {
    position: absolute; left: 23px; top: 172px;
    font-style: italic; font-size: 18px; color: var(--brand-red);
  }
  .contact-list { position: absolute; left: 22px; top: 214px; list-style: none; }
  .contact-item {
    display: flex; align-items: center; height: 32px;
    font-style: italic; font-size: 19px; letter-spacing: .4px; color: var(--ink);
  }
  .contact-item svg { width: 30px; height: 22px; margin-right: 6px; flex: none; }
  .brand-name {
    position: absolute; font-weight: 900; color: var(--brand-red);
    white-space: nowrap; transform: translateX(-50%);
    display: flex; align-items: center; gap: 8px;
  }
  .brand-name .brand-dot { width: 12px; height: 12px; background: var(--brand-red); }
  .card--front .brand-name { left: 524px; top: 180px; font-size: 22px; }
  .card--back .brand-name { left: 524px; top: 330px; font-size: 21px; }
</style>
</head>
<body>
<div class="canvas">
  <section class="card card--front">
    <div class="front-disc"></div>
    <p class="company-line">Talbert Stonecraft</p>
    <p class="person-name">MARA VOSS</p>
    <p class="person-role">Director</p>
    <ul class="contact-list">
      <li class="contact-item">
        <svg viewBox="0 0 30 22" aria-hidden="true"><path fill="#e8262b" d="M2 7c0-4 26-4 26 0v3h-6V7H8v3H2z M7 11h16l3 9H4z"/><circle cx="15" cy="15" r="3" fill="#c49a6c"/></svg>
        555-014-2290
      </li>
      <li class="contact-item">
        <svg viewBox="0 0 30 22" aria-hidden="true"><rect x="3" y="3" width="24" height="16" fill="#e8262b"/><path d="M3 4l12 9 12-9" fill="none" stroke="#c49a6c" stroke-width="2"/></svg>
        Talbertstonecraft@mailbrook.net
      </li>
      <li class="contact-item">
        <svg viewBox="0 0 30 22" aria-hidden="true"><rect x="4" y="1" width="23" height="16" fill="none" stroke="#e8262b" stroke-width="2"/><circle cx="15.5" cy="9" r="4" fill="none" stroke="#e8262b" stroke-width="1.5"/><path d="M11 21h9M15.5 17v4" stroke="#e8262b" stroke-width="2"/></svg>
        www.talbertstonecraft.net
      </li>
    </ul>
    <p class="brand-name"><span class="brand-dot"></span>TALBERT STONECRAFT</p>
  </section>
  <section class="card card--back">
    <p class="brand-name"><span class="brand-dot"></span>TALBERT STONECRAFT</p>
  </section>
</div>
</body>
</html>
```